Vindgerdi - Start-up company selling electricity

Hello let me tell you about Vindgerdi.

Vindgerdi is start-up company selling electricity in Iceland. The operations of the company consist of making power usage forecasts for our customers, purchasing the electricity wholesale from the energy producers, and selling the electricity to the consumer. We are focused on tech by using optimization and machine learning to minimize electricity prices to our customers. Our marketing strategy is to portray a tech company mindset and to show dedication to driving down the electricity price on the market.

We need your help to make our website pop. Possible concepts to work with are as follows:

- Iceland the land of ice and fire
- Green energy
- Innovation
- Tech and data science

Link to our website: https://prufa.vindgerdi-example.is/
We are open to ideas.
Thank you!

Target Market(s)

Electricity consumers both homes and companies.

Number of Pages Required

1 page

Font styles to use
Serif
Sans Serif

```html
<!DOCTYPE html>
<html lang="is">
<head>
<meta charset="utf-8">
<title>Vindgerdi</title>
<link href="https://fonts.googleapis.com/css2?family=Cinzel:wght@700&family=Poppins:wght@400;500;600&display=swap" rel="stylesheet">
<style>
:root{
  --navy:#0b3468;
  --navy-deep:#082a55;
  --red:#9a2e33;
  --red-soft:#b5474b;
  --grey:#7d7d7d;
  --text:#6f6f6f;
  --white:#fff;
}
*{margin:0;padding:0;box-sizing:border-box}
html,body{width:729px;height:1200px;overflow:hidden;background:var(--white)}
body{position:relative;font-family:"Poppins",sans-serif;color:var(--text)}
.abs{position:absolute}
.topbar{left:0;top:0;width:729px;height:22px;background:var(--navy);color:var(--white);font-size:7px;line-height:22px}
.topbar .welcome{left:37px}
.topbar .info{display:flex;align-items:center;gap:6px}
.topbar .dot{width:15px;height:15px;border-radius:50%;background:var(--white);display:flex;align-items:center;justify-content:center}
.header{left:0;top:22px;width:729px;height:49px;background:var(--white);border-bottom:1px solid var(--navy)}
.brand{display:flex;align-items:center;gap:6px;font-family:"Cinzel",serif;font-weight:700;color:var(--red)}
.brand .mark{border-radius:50%;background:var(--navy)}
.nav a{position:absolute;top:20px;font-size:7.3px;color:#555;text-decoration:none}
.nav a.active{color:var(--red)}
.nav a.active::after{content:"";position:absolute;left:50%;top:12px;width:6px;height:6px;margin-left:-3px;border-radius:50%;background:var(--navy)}
.pill{display:flex;align-items:center;justify-content:space-between;background:var(--red);color:var(--white);border-radius:14px;padding:0 3px 0 10px;font-size:8.5px;box-shadow:0 2px 4px rgba(0,0,0,.25)}
.pill .knob{width:19px;height:19px;border-radius:50%;background:var(--white);display:flex;align-items:center;justify-content:center}
.pill .knob i{width:8px;height:8px;border-radius:50%;background:var(--navy)}
.hero-title{left:0;width:729px;top:176px;text-align:center;font-family:"Cinzel",serif;font-weight:700;font-size:35px;color:var(--white);letter-spacing:1px;text-shadow:0 2px 4px rgba(0,0,0,.3)}
.hero-title span{color:var(--red)}
.hero-sub{left:0;width:729px;top:221px;text-align:center;color:var(--white);font-size:10px;line-height:15px;text-shadow:0 1px 3px rgba(0,0,0,.5)}
.feature-icon{width:61px;height:61px;border-radius:50%;border:1px solid var(--navy);display:flex;align-items:center;justify-content:center}
.feature h2{font-size:10.7px;font-weight:600;margin-bottom:6px}
.feature p{font-size:7.3px;line-height:12px;width:210px}
.btn{display:flex;align-items:center;justify-content:center;font-size:7.5px;font-weight:600;border-radius:2px}
.price{font-size:15.6px;color:#444}
.unit{font-size:7.3px}
.decor{left:452px;top:499px;width:240px;height:365px;border-radius:24px;background:linear-gradient(180deg,#c0675f 0%,#b8554a 38%,#1f3a6e 55%,#0c2654 100%)}
.footer h3{font-size:11px;font-weight:400;color:var(--white)}
.footer .link{font-size:7.3px;color:#f1d6d6}
.contact-ico{width:21px;height:21px;background:var(--white);border-radius:2px;display:flex;align-items:center;justify-content:center}
.bottombar{left:0;top:1177px;width:729px;height:23px;background:var(--navy);color:#dfe6f0;font-size:7px;line-height:23px;text-align:center}
</style>
</head>
<body>

<div class="abs topbar">
  <span class="abs welcome">Welcome To VINDGERDI!</span>
  <div class="abs info" style="left:480px"><span class="dot"><svg width="8" height="8" viewBox="0 0 24 24"><path fill="#9a2e33" d="M6.6 10.8a15 15 0 0 0 6.6 6.6l2.2-2.2c.3-.3.7-.4 1-.2 1.1.4 2.3.6 3.6.6.6 0 1 .4 1 1V20c0 .6-.4 1-1 1A17 17 0 0 1 3 4c0-.6.4-1 1-1h3.5c.6 0 1 .4 1 1 0 1.3.2 2.5.6 3.6.1.3 0 .7-.2 1z"/></svg></span>Call: 555-0199</div>
  <div class="abs info" style="left:582px"><span class="dot"><svg width="8" height="8" viewBox="0 0 24 24"><rect x="2" y="5" width="20" height="14" rx="2" fill="#9a2e33"/><rect x="5" y="9" width="5" height="5" fill="#fff"/><rect x="12" y="9" width="7" height="1.5" fill="#fff"/><rect x="12" y="12" width="5" height="1.5" fill="#fff"/></svg></span>ID Number: 123456-7890</div>
</div>

<header class="abs header">
  <div class="abs brand" style="left:37px;top:13px;font-size:20px"><span class="mark" style="width:18px;height:18px"></span>VINDGERDI</div>
  <nav class="nav">
    <a class="active" style="left:286px">Home</a>
    <a style="left:329px">Terms of Business</a>
    <a style="left:418px">Question &amp; Answer</a>
    <a style="left:510px">About Vindgerdi</a>
  </nav>
  <div class="abs pill" style="left:594px;top:12px;width:98px;height:25px">CONTACT US<span class="knob"><i></i></span></div>
</header>

<svg class="abs" style="left:0;top:71px" width="729" height="412" viewBox="0 71 729 412" role="img" aria-label="Photograph of a lakeside Icelandic town with a church under a blue evening sky, reflected in calm water">
  <defs>
    <linearGradient id="heroSky" x1="0" y1="0" x2="0" y2="1">
      <stop offset="0" stop-color="#0a3467"/>
      <stop offset=".45" stop-color="#2d67a8"/>
      <stop offset=".62" stop-color="#8aa9c6"/>
      <stop offset=".68" stop-color="#4d5a6b"/>
      <stop offset=".74" stop-color="#3d78b8"/>
      <stop offset="1" stop-color="#0d3a72"/>
    </linearGradient>
  </defs>
  <path d="M0 71H729V275C500 390 330 480 185 480C100 480 40 440 0 397Z" fill="url(#heroSky)"/>
  <path d="M729 275C500 390 330 480 185 480C100 480 40 440 0 397" fill="none" stroke="#9a2e33" stroke-width="1.5"/>
</svg>

<div class="abs hero-title">VIND <span>GERDI</span></div>
<div class="abs hero-sub">Vindgerdi reserves the right to change these<br>terms of business.</div>
<div class="abs pill" style="left:317px;top:264px;width:97px;height:26px">CONTACT US<span class="knob"><i></i></span></div>

<div class="abs feature-icon" style="left:36px;top:548px">
  <svg width="38" height="22" viewBox="0 0 38 22" fill="none" stroke="#0b3468" stroke-width="1.3"><path d="M2 4h5v12H2M36 4h-5v12h5M7 6l6-2 5 2 4-1 9 2M7 14l6 5c1 1 3 0 2-1l2 2c1 1 3 0 2-1l1 1c1 1 3 0 2-1l-1-2c1 1 3 0 2-1l6-3"/></svg>
</div>
<div class="abs feature" style="left:115px;top:558px">
  <h2 style="color:var(--navy)">Velkomin í viðskipti</h2>
  <p>Lorem Ipsum is simply dummy text of the printing and typesetting industry.</p>
</div>
<div class="abs btn" style="left:114px;top:608px;width:73px;height:25px;background:var(--navy);color:#fff">Fyrirtæki</div>
<div class="abs btn" style="left:196px;top:608px;width:64px;height:25px;border:1px solid var(--navy);color:var(--navy)">Heimili</div>

<div class="abs feature-icon" style="left:36px;top:662px;border-color:var(--red)">
  <svg width="30" height="28" viewBox="0 0 30 28" fill="none" stroke="#9a2e33" stroke-width="1.3"><path d="M3 4h15v21H3zM6 9h9M6 13h6M6 17h6M6 21h9"/><circle cx="21" cy="13" r="6" fill="#fff"/><path d="M23 10h-3a1.5 1.5 0 0 0 0 3h2a1.5 1.5 0 0 1 0 3h-3M21 9v8"/></svg>
</div>
<div class="abs feature" style="left:115px;top:672px"><h2 style="color:var(--red)">Verðskrá</h2></div>
<div class="abs" style="left:122px;top:688px"><div class="price">6.98</div></div>
<div class="abs unit" style="left:115px;top:709px">krónur / kWst</div>
<div class="abs" style="left:182px;top:690px;width:1px;height:30px;background:#ddd"></div>
<div class="abs" style="left:209px;top:688px"><div class="price">6.25</div></div>
<div class="abs unit" style="left:202px;top:709px">krónur / kWst</div>
<div class="abs unit" style="left:115px;top:732px;line-height:12px">rafmagnskynding<br>Gerðu verðsamanburð</div>
<div class="abs btn" style="left:214px;top:731px;width:73px;height:25px;background:var(--red);color:#fff">Verðvaki</div>

<div class="abs feature-icon" style="left:36px;top:790px;border-color:var(--grey)">
  <svg width="34" height="26" viewBox="0 0 34 26" fill="none" stroke="#7d7d7d" stroke-width="1.2"><path d="M6 13a11 11 0 0 1 20-6M28 13a11 11 0 0 1-20 6M24 4l2 3 3-2M10 22l-2-3-3 2M18 6l-4 8h5l-3 7"/></svg>
</div>
<div class="abs feature" style="left:115px;top:800px">
  <h2 style="color:#555">Framtíðin er spennandi</h2>
  <p>Gerum raforkukerfið snallara saman. Vindgerdi notar gervigreind, gagnavísindi og sjálfvirkni til að lágmarka kostnað og stuðla að okrujöfnuði</p>
</div>
<div class="abs btn" style="left:114px;top:863px;width:73px;height:25px;background:var(--grey);color:#fff">Vita Meira</div>

<div class="abs decor" role="img" aria-label="Photographic collage of a sunlit mountain ridge above a night view of the earth with glowing network lines"></div>

<svg class="abs" style="left:0;top:870px" width="729" height="307" viewBox="0 870 729 307">
  <path d="M0 957C200 1000 480 998 620 960C690 940 729 900 729 880V1177H0Z" fill="#9a2e33"/>
</svg>

<footer class="footer">
  <div class="abs brand" style="left:37px;top:1022px;font-size:16px;color:#fff"><span class="mark" style="width:15px;height:15px;background:#fff"></span>VINDGERDI</div>
  <p class="abs link" style="left:37px;top:1048px;width:150px;line-height:12px">Our marketing strategy is to portray a tech company mindset and to show dedication to driving down the electricity price on the market.</p>

  <h3 class="abs" style="left:205px;top:1017px">Site Map</h3>
  <span class="abs link" style="left:205px;top:1038px">- Home</span>
  <span class="abs link" style="left:205px;top:1056px">- Terms of Business</span>
  <span class="abs link" style="left:205px;top:1074px">- Question &amp; Answer</span>
  <span class="abs link" style="left:205px;top:1092px">- About Vindgerdi</span>

  <h3 class="abs" style="left:372px;top:1017px">Contact Us</h3>
  <div class="abs contact-ico" style="left:371px;top:1039px"><svg width="11" height="12" viewBox="0 0 24 24" fill="none" stroke="#9a2e33" stroke-width="2"><path d="M12 22s7-7 7-12a7 7 0 0 0-14 0c0 5 7 12 7 12z"/><circle cx="12" cy="10" r="2.5"/></svg></div>
  <span class="abs link" style="left:400px;top:1043px;font-family:Arial,sans-serif">Hafnargata 21 220 Dalvík</span>
  <div class="abs contact-ico" style="left:371px;top:1071px"><svg width="12" height="10" viewBox="0 0 24 18"><rect width="24" height="18" rx="2" fill="#9a2e33"/><path d="M2 3l10 7 10-7" fill="none" stroke="#fff" stroke-width="2"/></svg></div>
  <span class="abs link" style="left:400px;top:1075px;font-family:Arial,sans-serif">info@vindgerdi-example.is</span>
  <div class="abs contact-ico" style="left:371px;top:1103px"><svg width="11" height="11" viewBox="0 0 24 24"><path fill="#9a2e33" d="M6.6 10.8a15 15 0 0 0 6.6 6.6l2.2-2.2c.3-.3.7-.4 1-.2 1.1.4 2.3.6 3.6.6.6 0 1 .4 1 1V20c0 .6-.4 1-1 1A17 17 0 0 1 3 4c0-.6.4-1 1-1h3.5c.6 0 1 .4 1 1 0 1.3.2 2.5.6 3.6.1.3 0 .7-.2 1z"/></svg></div>
  <span class="abs link" style="left:400px;top:1109px;font-family:Arial,sans-serif">555-0199</span>

  <h3 class="abs" style="left:540px;top:1017px">Terms of Business</h3>
  <span class="abs link" style="left:540px;top:1043px">- Scope</span>
  <span class="abs link" style="left:540px;top:1057px">- Gathering information and plan</span>
  <span class="abs link" style="left:540px;top:1070px">- Dealer change</span>
  <span class="abs link" style="left:540px;top:1084px">- User exchange</span>
  <span class="abs link" style="left:540px;top:1098px">- Prices and payment terms</span>
  <span class="abs link" style="left:540px;top:1111px">- End of contractual relationship</span>
  <span class="abs link" style="left:540px;top:1125px">- Privacy</span>
  <span class="abs link" style="left:540px;top:1139px">- Uncontrollable events</span>
</footer>

<div class="abs bottombar">©2021 VINDGERDI - All Right Reserved.</div>

</body>
</html>
```